Customizable Form Generation Website

This will be a place for users to quickly generate numerous forms from a categorized list. As the forms are templates with field variables, the site must be able to substitute ‘real data’ for template variable data. This tool will allow for quick custom forms on-demand.

The landing page is attached. We need the User Experience and User Interface solved for us.

EXAMPLE:
——————————————————————-
Dear {{PatientFirstName}},

Please come back for an examination on {{SelectedDate}} with Doctor {{SelectedProvider}}.

Sincerely,

{{SelectedAuthor}}
——————————————————————-

Coming to the Forms Landing Page, the user will see the forms available to select. The user will then click to select a form.

At some point, the user must resolve the variables in the form. For instance, there are the following variables in the above example: PatientFirstName, SelectedDate, SelectedProvider, and SelectedAuthor. We must give the user a chance to select the values for these variables. Using a dropdown combobox will probably work for most. Getting a date selector will be required if the variable happens to contain the string 'date'.

Is it best to preselect common variables before opening the form, or is it best to dynamically scan the template, then give the user the option to give values to each variable found?

The design must include a way for users to upload additional forms. Forms will most probably be PDF, .DOC, .TXT files. This allows users to develop simple or fancy forms of their choosing., then simply drop them into the site for future use.

The design must include a way for users to create new forms. The form creation tool must present to the user the list of predefined variables like {{PatientLastName}} for easy insertion into the form writer. Anytime "{{}}" are used, developers will recognize that as a variable that needs to be resolved.

The forms will be separated into categories as follows:

OFFICE:
- Letterhead
- Sign-In Sheet
- Fax Cover Sheet
SCHEDULER:
- Appointment Reminder
- Missed Appointment Policy
PATIENT:
- Intake Form
- Patient Discharge
- Return to Work or School
- Excuse Slip
- Consent to Treat a Minor
- Verify Non-Pregnancy
RELEASE:
- Health Information Release Form
- X-Ray Release Form
CERTIFICATES:
- Certificate of Care
- Disability Certificate
INSURANCE:
- Authorization to Bill Insurance
- Assignment Authorization
OTHER:
- Free Massage
- Free Vitamins

The design must include a way to add/customize categories. Categories are for organizing the forms logically.

We welcome ANY questions to help understand the requirements.

Good luck!

Healthcare

3 page

• Must Follow TESSERA LAYOUT standards
• Great User Experience. Simple, Fast, Clever.
• nothing to add here

```html
<!DOCTYPE html>
<html lang="en">
<head>
<meta charset="utf-8">
<title>ClinicForge – Forms</title>
<link href="https://fonts.googleapis.com/css2?family=Roboto:wght@400;500;700&display=swap" rel="stylesheet">
<style>
  :root{
    --page:#bababa;
    --navy:#011a28;
    --orange:#ff5e00;
    --orange-2:#ff7a00;
    --strip:#9fb0bd;
    --canvas:#ece9e7;
    --white:#ffffff;
    --ink:#0e1a24;
  }
  *{box-sizing:border-box;margin:0;padding:0}
  html,body{width:1056px;height:1200px;overflow:hidden}
  body{background:var(--page);font-family:"Roboto",sans-serif;color:var(--ink);position:relative}
  .screen{position:absolute;left:78px;width:900px;height:483px;background:var(--canvas);overflow:hidden}
  .screen--letter{top:85px}
  .screen--forms{top:632px}
  .topbar{position:absolute;left:0;top:0;width:100%;height:66px;background:var(--navy);color:var(--white)}
  .brand{position:absolute;left:22px;top:19px;display:flex;align-items:center;gap:9px}
  .brand__dot{width:22px;height:22px;border-radius:50%;background:var(--orange)}
  .brand__name{font-size:19px;font-weight:700;color:#e9edf0;letter-spacing:-.3px}
  .topbar__tools{position:absolute;right:32px;top:17px;display:flex;align-items:center;height:32px;font-size:10px}
  .topbar__tools svg{display:block}
  .flag{width:26px;height:26px;border-radius:50%;background:linear-gradient(180deg,#3b4f9a 0 45%,#e0343c 45% 60%,#f2f2f2 60% 75%,#e0343c 75%);margin-left:20px}
  .lang{margin-left:6px;display:flex;align-items:center;gap:3px}
  .bell{margin-left:18px}
  .avatar{width:26px;height:26px;border-radius:50%;background:linear-gradient(160deg,#c9b8a8,#5d4a3c);margin-left:20px}
  .user{margin-left:6px}
  .sidebar{position:absolute;left:0;top:66px;width:134px;bottom:0;background:linear-gradient(180deg,var(--orange),var(--orange-2));border-right:5px solid var(--strip);width:139px}
  .menu{list-style:none;position:absolute;left:26px;top:24px}
  .menu li{display:flex;align-items:center;height:28px;color:var(--white);font-size:9.5px}
  .menu svg{width:10px;height:10px;margin-right:9px;fill:var(--white)}
  /* letter screen */
  .letter{position:absolute;left:167px;top:92px;width:712px;height:168px;background:var(--white);border-radius:3px;box-shadow:4px 4px 0 var(--navy);padding:0 21px}
  .letter__greeting{position:absolute;left:21px;top:20px;font-size:19px;font-weight:700}
  .letter__line{position:absolute;left:21px;top:54px;display:flex;align-items:center;font-size:14px;font-weight:500;white-space:nowrap}
  .select{display:flex;align-items:center;justify-content:space-between;height:35px;border:2px solid var(--navy);border-radius:18px;padding:0 16px 0 20px;font-size:8.5px;font-weight:400;margin:0 12px}
  .select--date{width:116px}
  .select--provider{width:135px;margin-right:0}
  .letter__sign{position:absolute;left:21px;top:102px;font-size:14px;font-weight:700}
  .letter__author{position:absolute;left:21px;top:128px;font-size:14px}
  /* forms screen */
  .cat{position:absolute;top:80px;width:90px;margin-left:-45px;text-align:center}
  .cat__ring{width:76px;height:76px;margin:0 auto;border:4px solid var(--orange);border-radius:50%;background:var(--white);display:flex;align-items:center;justify-content:center}
  .cat__ring svg{width:40px;height:40px;fill:var(--navy)}
  .cat__label{margin-top:9px;font-size:11px;font-weight:700;letter-spacing:.2px}
  .pointer{position:absolute;left:265px;top:189px;width:0;height:0;border-left:6px solid transparent;border-right:6px solid transparent;border-bottom:11px solid var(--strip)}
  .panel{position:absolute;left:163px;top:203px;width:643px;height:223px;background:var(--white);border-radius:8px;box-shadow:0 1px 4px rgba(0,0,0,.12)}
  .tile{position:absolute;top:35px;width:154px;text-align:center}
  .tile__preview{height:141px;border-radius:7px}
  .tile__name{margin-top:9px;font-size:12px;font-weight:700}
  .preview--letterhead{background:linear-gradient(180deg,#d6d8dc,#cfd2d6)}
  .preview--signin{background:linear-gradient(180deg,#e9b393 0%,#8fa7d8 35%,#3b66b3 100%)}
  .preview--fax{background:linear-gradient(135deg,#b6aa98,#efe5d6)}
</style>
</head>
<body>

<!-- Letter screen -->
<section class="screen screen--letter">
  <header class="topbar">
    <div class="brand"><span class="brand__dot"></span><span class="brand__name">ClinicForge</span></div>
    <div class="topbar__tools">
      <svg width="10" height="10" viewBox="0 0 24 24"><circle cx="10" cy="10" r="7" fill="none" stroke="#fff" stroke-width="3"/><path d="M15 15l6 6" stroke="#fff" stroke-width="3.5"/></svg>
      <span class="flag" role="img" aria-label="US flag"></span>
      <span class="lang">English <svg width="7" height="7" viewBox="0 0 10 10"><path d="M1 3l4 4 4-4" fill="none" stroke="#fff" stroke-width="1.5"/></svg></span>
      <svg class="bell" width="10" height="11" viewBox="0 0 24 26"><path d="M12 2a7 7 0 0 0-7 7v6l-3 4h20l-3-4V9a7 7 0 0 0-7-7zM9 22a3 3 0 0 0 6 0z" fill="#fff"/></svg>
      <span class="avatar" role="img" aria-label="User profile photo"></span>
      <span class="user">John doe</span>
    </div>
  </header>
  <nav class="sidebar">
    <ul class="menu">
      <li><svg viewBox="0 0 24 24"><path d="M12 3L1 13h3v8h6v-6h4v6h6v-8h3z"/></svg>Home</li>
      <li><svg viewBox="0 0 24 24"><path d="M2 21h20v2H2zM3 4h2v15H3zM8 10h3v9H8zM13 6h3v13h-3zM18 12h3v7h-3z"/></svg>Support</li>
      <li><svg viewBox="0 0 24 24"><path d="M2 4h5v4H2zM9 4h13v4H9zM2 10h5v4H2zM9 10h13v4H9zM2 16h5v4H2zM9 16h13v4H9z"/></svg>Signs</li>
      <li><svg viewBox="0 0 24 24"><path d="M1 3h4l3 12h12l3-9H7" /><path d="M1 2h4l1 3h17l-3 10H8l-3-11H1z"/><circle cx="9" cy="20" r="2"/><circle cx="18" cy="20" r="2"/></svg>Purchases</li>
      <li><svg viewBox="0 0 24 24"><circle cx="12" cy="7" r="5"/><path d="M3 23c0-6 4-9 9-9s9 3 9 9z"/></svg>Admin/Account</li>
      <li><svg viewBox="0 0 24 24"><path d="M10 1h4l1 3 3 2 3-1 2 4-2 2v2l2 2-2 4-3-1-3 2-1 3h-4l-1-3-3-2-3 1-2-4 2-2v-2L1 9l2-4 3 1 3-2z"/><circle cx="12" cy="12" r="3.5" fill="#ff6a00"/></svg>Setting</li>
      <li><svg viewBox="0 0 24 24"><path d="M1 4l7-2v18l-7 2zM9 2l6 2v18l-6-2zM16 4l7-2v18l-7 2z"/></svg>State</li>
    </ul>
  </nav>

  <article class="letter">
    <h1 class="letter__greeting">Dear John doe,</h1>
    <div class="letter__line">
      Please come back for an examination on
      <span class="select select--date">SelectedDate <svg width="8" height="8" viewBox="0 0 10 10"><path d="M1 3l4 4 4-4" fill="none" stroke="#011a28" stroke-width="1.6"/></svg></span>
      With Doctor
      <span class="select select--provider">SelectedProvider <svg width="8" height="8" viewBox="0 0 10 10"><path d="M1 3l4 4 4-4" fill="none" stroke="#011a28" stroke-width="1.6"/></svg></span>
    </div>
    <p class="letter__sign">Sincerely,</p>
    <p class="letter__author">John doe</p>
  </article>
</section>

<!-- Forms landing screen -->
<section class="screen screen--forms">
  <header class="topbar">
    <div class="brand"><span class="brand__dot"></span><span class="brand__name">ClinicForge</span></div>
    <div class="topbar__tools">
      <svg width="10" height="10" viewBox="0 0 24 24"><circle cx="10" cy="10" r="7" fill="none" stroke="#fff" stroke-width="3"/><path d="M15 15l6 6" stroke="#fff" stroke-width="3.5"/></svg>
      <span class="flag" role="img" aria-label="US flag"></span>
      <span class="lang">English <svg width="7" height="7" viewBox="0 0 10 10"><path d="M1 3l4 4 4-4" fill="none" stroke="#fff" stroke-width="1.5"/></svg></span>
      <svg class="bell" width="10" height="11" viewBox="0 0 24 26"><path d="M12 2a7 7 0 0 0-7 7v6l-3 4h20l-3-4V9a7 7 0 0 0-7-7zM9 22a3 3 0 0 0 6 0z" fill="#fff"/></svg>
      <span class="avatar" role="img" aria-label="User profile photo"></span>
      <span class="user">John doe</span>
    </div>
  </header>
  <nav class="sidebar">
    <ul class="menu">
      <li><svg viewBox="0 0 24 24"><path d="M12 3L1 13h3v8h6v-6h4v6h6v-8h3z"/></svg>Home</li>
      <li><svg viewBox="0 0 24 24"><path d="M2 21h20v2H2zM3 4h2v15H3zM8 10h3v9H8zM13 6h3v13h-3zM18 12h3v7h-3z"/></svg>Support</li>
      <li><svg viewBox="0 0 24 24"><path d="M2 4h5v4H2zM9 4h13v4H9zM2 10h5v4H2zM9 10h13v4H9zM2 16h5v4H2zM9 16h13v4H9z"/></svg>Signs</li>
      <li><svg viewBox="0 0 24 24"><path d="M1 2h4l1 3h17l-3 10H8l-3-11H1z"/><circle cx="9" cy="20" r="2"/><circle cx="18" cy="20" r="2"/></svg>Purchases</li>
      <li><svg viewBox="0 0 24 24"><circle cx="12" cy="7" r="5"/><path d="M3 23c0-6 4-9 9-9s9 3 9 9z"/></svg>Admin/Account</li>
      <li><svg viewBox="0 0 24 24"><path d="M10 1h4l1 3 3 2 3-1 2 4-2 2v2l2 2-2 4-3-1-3 2-1 3h-4l-1-3-3-2-3 1-2-4 2-2v-2L1 9l2-4 3 1 3-2z"/><circle cx="12" cy="12" r="3.5" fill="#ff6a00"/></svg>Setting</li>
      <li><svg viewBox="0 0 24 24"><path d="M1 4l7-2v18l-7 2zM9 2l6 2v18l-6-2zM16 4l7-2v18l-7 2z"/></svg>State</li>
    </ul>
  </nav>

  <div class="cat" style="left:194px">
    <div class="cat__ring"><svg viewBox="0 0 24 24"><path d="M2 2h11v20H2zM14 9h8v13h-8z"/><path d="M4 5h2v2H4zM8 5h2v2H8zM4 9h2v2H4zM8 9h2v2H8zM4 13h2v2H4zM8 13h2v2H8zM16 12h2v2h-2zM16 16h2v2h-2zM6 18h3v4H6z" fill="#fff"/></svg></div>
    <p class="cat__label">OFFICE:</p>
  </div>
  <div class="cat" style="left:303px">
    <div class="cat__ring"><svg viewBox="0 0 24 24"><path d="M2 4h18v6a8 8 0 0 0-9 12H2z"/><path d="M6 1h2v4H6zM14 1h2v4h-2z"/><circle cx="17" cy="17" r="6"/><path d="M16.3 13.5h1.4v3.3l2.3 1.4-.7 1.2-3-1.8z" fill="#fff"/></svg></div>
    <p class="cat__label">SCHEDULER:</p>
  </div>
  <div class="cat" style="left:411px">
    <div class="cat__ring"><svg viewBox="0 0 24 24"><circle cx="10" cy="6" r="5"/><path d="M1 21c0-6 4-9 9-9 3 0 5 1 6 3h-4l-2 3-1-1H1z"/><path d="M8 19h3l2-3 2 5 2-3h6" fill="none" stroke="#011a28" stroke-width="2"/></svg></div>
    <p class="cat__label">PATIENT:</p>
  </div>
  <div class="cat" style="left:520px">
    <div class="cat__ring"><svg viewBox="0 0 24 24"><circle cx="12" cy="7" r="4"/><circle cx="12" cy="7" r="1.6" fill="#fff"/><path d="M11 1h2v2h-2zM11 11h2v2h-2zM6 6h2v2H6zM16 6h2v2h-2z"/><path d="M3 14l9 2 9-2v9H3zM19 1l3 4h-2v5h-2V5h-2zM4 13V9h2v4h2l-3 3-3-3z"/></svg></div>
    <p class="cat__label">RELEASE:</p>
  </div>
  <div class="cat" style="left:628px">
    <div class="cat__ring"><svg viewBox="0 0 24 24"><path d="M1 4h18l4 4v8h-5a5 5 0 0 0-9 0v1H1z"/><path d="M4 8h10v1.5H4zM4 11h8v1.5H4z" fill="#fff"/><circle cx="14" cy="17" r="3.5"/><path d="M12 20l-1 4 3-1.5 3 1.5-1-4z"/></svg></div>
    <p class="cat__label">CERTIFICATES:</p>
  </div>
  <div class="cat" style="left:737px">
    <div class="cat__ring"><svg viewBox="0 0 24 24"><path d="M12 1l10 4v6c0 6-4 10-10 12C6 21 2 17 2 11V5z"/><path d="M12 4l7 3v4c0 5-3 8-7 9.5C8 19 5 16 5 11V7z" fill="#fff"/><path d="M8 12l3 3 5-6" fill="none" stroke="#011a28" stroke-width="2"/></svg></div>
    <p class="cat__label">INSURANCE:</p>
  </div>
  <div class="cat" style="left:845px">
    <div class="cat__ring"><svg viewBox="0 0 24 24"><circle cx="12" cy="12" r="11"/><path d="M12 3v7M20 8l-6 3M19 17l-6-4M9 20l2-7M4 13l6-2M7 4l4 6" stroke="#fff" stroke-width="2"/></svg></div>
    <p class="cat__label">OTHER:</p>
  </div>

  <span class="pointer"></span>
  <div class="panel">
    <div class="tile" style="left:25px">
      <div class="tile__preview preview--letterhead" role="img" aria-label="Letterhead template preview"></div>
      <p class="tile__name">Letterhead</p>
    </div>
    <div class="tile" style="left:245px">
      <div class="tile__preview preview--signin" role="img" aria-label="Sign-in sheet template preview"></div>
      <p class="tile__name">Sign-In Sheet</p>
    </div>
    <div class="tile" style="left:465px">
      <div class="tile__preview preview--fax" role="img" aria-label="Fax cover sheet template preview"></div>
      <p class="tile__name">Fax Cover Sheet</p>
    </div>
  </div>
</section>

</body>
</html>
```